New Electrical Contractor looking for local work

I have just started working for myself as an Electrical Contractor, based in the eastern suburbs of Melbourne. I want to advertise in the local area so hopefully I can create a client base that is close to home, so I thought a flyer that I could drop in letterboxes could be a good start. Most of my experience has been domestic houses, so ideally this is the work I would like to get more of.

Here is a list of the work I usually do:
Extensions / Renovations
Safety Switch and Switchboard Upgrades
LED Lighting including downlights/light fittings and LED strip light
Re-wires
Maintenance

I have also added a couple of images of LED strip lights and how they can be used in homes. There are a lot more on google images if anyone thinks they could be of use.

These are my details:
Business name - Dirk Malan Electrical
Phone - 0437 218 064
ABN - 41 382 704 916
REC - 58317
Email - malanelectrical@brivomail.net

I will attach my business logo and business card
Updates

Could I please ask for all designs to delete the "(contractors registration number)" text.

Only REC 58317 needs to be displayed.

Thank you kindly

Industry/Entity Type

Business

Requirements
Must have
• My contact details, ie. Name, Phone, email, ABN, REC etc

```html
<!DOCTYPE html>
<html lang="en">
<head>
<meta charset="utf-8">
<title>Dirk Malan Electrical – Flyer</title>
<link rel="stylesheet" href="https://fonts.googleapis.com/css2?family=Alfa+Slab+One&family=Arimo:wght@700&family=Tinos:wght@700&display=swap">
<style>
  :root {
    --brand-red: #e3161c;
    --paper: #ffffff;
    --blue-deep: #0a3f9e;
    --blue-mid: #1f6fd6;
    --blue-light: #9cc8f2;
    --photo-warm: #8a5a2e;
    --photo-dark: #2a2430;
    --photo-blue: #2f3f8f;
    --photo-light: #d9d6d0;
  }
  html, body { margin: 0; padding: 0; overflow: hidden; }
  .flyer {
    position: relative;
    width: 1200px;
    height: 894px;
    background: var(--paper);
    overflow: hidden;
  }
  .swoosh { position: absolute; inset: 0; }
  .logo-art {
    position: absolute; left: 28px; top: 10px; width: 72px; height: 152px;
    background: linear-gradient(180deg, #e8e8e8, #b8b8b8);
    border-radius: 36px 36px 14px 14px;
  }
  .headline {
    position: absolute; left: 180px; top: 16px; margin: 0;
    font-family: "Alfa Slab One", serif; font-weight: 400;
    font-size: 72px; letter-spacing: 0; color: var(--brand-red);
    line-height: 1; white-space: nowrap;
  }
  .tagline {
    position: absolute; left: 278px; top: 108px; margin: 0;
    font-family: "Arimo", sans-serif; font-weight: 700;
    font-size: 46px; color: var(--brand-red); letter-spacing: 0.5px;
    white-space: nowrap;
  }
  .gallery { position: absolute; left: 0; top: 0; }
  .photo { position: absolute; }
  .photo.hall { left: 42px; top: 184px; width: 366px; height: 136px; background: linear-gradient(90deg, #3b3f7a, #6e5a8a 45%, #c9b77a); }
  .photo.kitchen { left: 429px; top: 184px; width: 346px; height: 136px; background: linear-gradient(180deg, var(--photo-dark), var(--photo-warm)); }
  .photo.stairs { left: 796px; top: 184px; width: 366px; height: 136px; background: linear-gradient(135deg, #10163a, var(--photo-blue) 60%, #5d7ae0); }
  .photo.cellar { left: 42px; top: 335px; width: 366px; height: 136px; background: linear-gradient(180deg, #5a3a1c, #b88550); }
  .photo.wiring { left: 429px; top: 335px; width: 346px; height: 136px; background: linear-gradient(90deg, #c9b29a, #8d8f93 55%, #e0ddd6); }
  .photo.switch-fix { left: 796px; top: 335px; width: 366px; height: 136px; background: linear-gradient(90deg, var(--photo-light), #bfa893); }
  .photo.downlight { left: 42px; top: 494px; width: 366px; height: 145px; background: linear-gradient(135deg, #cfc8bc, #f2f2f2 50%, #7d6a52); }
  .photo.strip-rolls { left: 429px; top: 494px; width: 346px; height: 145px; background: linear-gradient(180deg, #d8d2c4, #e6c35a 60%, #a8a090); }
  .photo.rgb-strip { left: 796px; top: 494px; width: 366px; height: 145px; background: linear-gradient(90deg, #111, #3a1f5e 40%, #1f6a6a 70%, #111); }
  .services {
    position: absolute; left: 42px; top: 652px; margin: 0; padding: 0;
    list-style: none; font-family: "Tinos", serif; font-weight: 700;
    font-size: 31px; line-height: 38px; color: var(--brand-red);
  }
  .contact {
    position: absolute; left: 766px; top: 664px; margin: 0;
    font-family: "Tinos", serif; font-weight: 700; font-style: normal;
    font-size: 32px; line-height: 49px; color: var(--brand-red);
  }
  .contact p { margin: 0; white-space: nowrap; }
  .contact .email { font-size: 23px; }
</style>
</head>
<body>
<main class="flyer">
  <svg class="swoosh" width="1200" height="894" viewBox="0 0 1200 894" aria-hidden="true">
    <defs>
      <linearGradient id="blueSweep" x1="0" y1="0" x2="1" y2="1">
        <stop offset="0" stop-color="#1f6fd6"/>
        <stop offset="1" stop-color="#0a3f9e"/>
      </linearGradient>
    </defs>
    <path d="M1060 0 C1010 200 1080 420 1200 560 L1200 0 Z" fill="url(#blueSweep)"/>
    <path d="M980 0 C960 240 1060 520 1200 700 L1200 640 C1090 480 1020 260 1040 0 Z" fill="#9cc8f2"/>
    <path d="M900 0 C900 300 1020 620 1200 840 L1200 760 C1050 560 960 320 955 0 Z" fill="#1f6fd6" opacity="0.85"/>
    <path d="M760 894 C900 820 1060 760 1200 740 L1200 894 Z" fill="url(#blueSweep)"/>
    <path d="M660 894 C820 800 1000 720 1200 700 L1200 720 C1010 745 850 815 720 894 Z" fill="#9cc8f2"/>
  </svg>

  <div class="logo-art" role="img" aria-label="Hand-drawn light bulb with fingers making an OK sign"></div>
  <h1 class="headline">Dirk Malan Electrical</h1>
  <p class="tagline">For All Your Electrical Needs</p>

  <section class="gallery">
    <div class="photo hall" role="img" aria-label="Hallways lit with LED strip lighting"></div>
    <div class="photo kitchen" role="img" aria-label="Kitchen with under-cabinet LED lighting"></div>
    <div class="photo stairs" role="img" aria-label="Staircase with blue LED step lights"></div>
    <div class="photo cellar" role="img" aria-label="Wine rack with warm LED lighting"></div>
    <div class="photo wiring" role="img" aria-label="Hands connecting electrical wires in conduit"></div>
    <div class="photo switch-fix" role="img" aria-label="Electrician fitting a wall switch with a screwdriver"></div>
    <div class="photo downlight" role="img" aria-label="LED downlight globe over a dining room"></div>
    <div class="photo strip-rolls" role="img" aria-label="Rolls of LED strip light"></div>
    <div class="photo rgb-strip" role="img" aria-label="Colour-changing RGB LED strip light"></div>
  </section>

  <ul class="services">
    <li>Extensions / Renovations</li>
    <li>Safety Switch and Switchboard Upgrades</li>
    <li>LED&nbsp; Lighting Including Downlights</li>
    <li>light fittings and LED strip light</li>
    <li>Re-wires</li>
    <li>Maintenance</li>
  </ul>

  <address class="contact">
    <p>Tel : - 0437 218 064</p>
    <p>ABN - 41 382 704 916</p>
    <p>REC - 58317</p>
    <p class="email">Email - malanelectrical@brivomail.net</p>
  </address>
</main>
</body>
</html>
```